Larkhollow needs a Webpage Design

We need a webpage for Dr. XYZ who is doing consultancy practice in the area of speech, language, and reading disabilities. He is doing his consultancy practice as "Larkhollow Consultants". Our target market is clients with annual income of $100,000 or more in Chicago area. Our business philosophy is: "...We provide the best evidence-based services/interventions, at an affordable fee, and deal only with clients who seek such services...."

Dr. XYZ's area of research interests are: a) using assistive technology for communication for children with autism, b) early intervention with focus on parent participation, and c) language learning for children birth-to-five years.

He works at a public university whose school color is 'Orange". Home page should show two logos (university and practice). Each page should stand on its own and reflect the content with minimal scrolling. The colors should be subdued (not bright colors) to attract college educated wealthy individuals who are seeking best evidence-based practice in speech, language, and reading for their children.

We need five pages: Home, Consultation, Research, Professional Development, and Contact (with google map directions). The home page should have space for a picture and links for facebook, twitter, and google plus. Other pages should have space for at least one picture and links to pdf files.

The overall design should show healthcare service, evidence-based early intervention with focus on parent participation, and project that we are leaders in the field.

```html
<!DOCTYPE html>
<html lang="en">
<head>
<meta charset="utf-8">
<title>Larkhollow Consultants</title>
<link href="https://fonts.googleapis.com/css2?family=Mulish:wght@400;500;600;700&display=swap" rel="stylesheet">
<style>
:root{
  --blue:#1b78d8;
  --ink:#333;
  --text:#555;
  --muted:#777;
  --nav:#3b3b3b;
  --nav-dark:#2c2c2c;
  --band:#f2f2f2;
  --line:#e2e2e2;
  --white:#fff;
}
*{margin:0;padding:0;box-sizing:border-box}
html,body{width:814px;height:1200px;overflow:hidden;background:var(--white)}
body{font-family:"Mulish",sans-serif;color:var(--text);position:relative}
a{color:inherit;text-decoration:none}
.abs{position:absolute}

.brand{left:88px;top:18px;width:148px}
.brand-name{font-size:28px;font-weight:600;color:var(--blue);line-height:1;letter-spacing:-.3px}
.brand-sub{font-size:16px;font-weight:400;color:#555;text-align:right;line-height:1.35}
.doctor{left:378px;top:50px;font-size:17px;color:var(--ink);font-weight:400}
.doctor span{color:var(--blue)}
.email{left:88px;top:86px;font-size:13px;color:var(--ink);display:flex;align-items:center;gap:6px}
.email a{color:var(--blue);margin-left:3px}

.nav{left:88px;top:126px;width:637px;height:35px;background:linear-gradient(var(--nav),var(--nav-dark));display:flex;border-radius:2px 2px 0 0}
.nav a{color:#fff;font-size:11px;font-weight:400;display:flex;align-items:center;justify-content:center;border-right:1px solid #555;height:100%}
.nav a:last-child{border-right:0}

.hero{left:88px;top:161px;width:637px;height:292px;background:linear-gradient(120deg,#c98a86 0%,#e0b7a0 30%,#8a9a6a 55%,#b8c0ae 75%,#c9463f 100%)}
.hero-shadow{left:100px;top:453px;width:613px;height:10px;background:radial-gradient(ellipse at top,rgba(0,0,0,.22),transparent 70%)}
.caption{left:88px;top:239px;width:418px;height:83px;background:rgba(255,255,255,.85);padding:4px 18px;font-size:21px;line-height:24px;color:var(--blue);font-weight:400}
.dots{left:381px;top:429px;display:flex;gap:4px}
.dots i{width:10px;height:10px;border-radius:50%;background:#222;display:block}

.h2{font-size:18px;font-weight:400;color:var(--ink);text-align:center}
.welcome-title{left:0;top:486px;width:814px}
.welcome-text{left:88px;top:520px;width:637px;font-size:9.8px;line-height:15.7px;text-align:center;color:var(--text)}
.more{font-size:10px;font-weight:500;color:var(--blue);text-align:center;border-bottom:3px solid #bbb;padding-bottom:6px}
.welcome-more{left:353px;top:583px;width:108px}

.band{left:0;top:619px;width:814px;height:311px;background:var(--band)}
.what-title{left:0;top:637px;width:814px}
.card{top:679px;width:203px;height:233px;background:var(--white);border:1px solid var(--line);padding:12px 10px;text-align:center}
.card-shadow{top:912px;width:183px;height:8px;background:radial-gradient(ellipse at top,rgba(0,0,0,.18),transparent 70%)}
.card-img{height:99px;width:180px;margin:0 auto}
.card h3{font-size:11.6px;font-weight:500;color:var(--blue);margin-top:13px;white-space:nowrap}
.card p{font-size:9.4px;line-height:15.6px;color:var(--text);margin-top:1px}
.card .learn{display:block;font-size:9.4px;color:var(--blue);font-weight:500;margin-top:5px}

.sec-title{font-size:18px;font-weight:400;color:var(--ink);white-space:nowrap}
.research-title{left:88px;top:950px}
.research-img{left:88px;top:990px;width:149px;height:102px;background:linear-gradient(135deg,#f4f1ea,#d9d4c8);border:1px solid var(--line)}
.bullets{left:258px;top:988px;width:250px;list-style:none}
.bullets li{font-size:9.6px;line-height:14px;color:var(--text);padding-left:18px;position:relative;margin-bottom:8px}
.bullets svg{position:absolute;left:0;top:3px}
.research-more{left:258px;top:1075px;width:110px;text-align:left}

.pd-title{left:480px;top:950px;width:245px;text-align:right}
.pd-item{left:520px;width:205px;display:flex;gap:8px;border-bottom:1px solid var(--line);padding-bottom:6px}
.pd-thumb{width:51px;height:51px;flex:none}
.pd-item p{font-size:8.4px;line-height:10.8px;color:var(--text)}
.pd-item b{display:block;font-size:8.4px;font-weight:500;color:var(--blue);margin-top:9px}

.footer{left:0;top:1127px;width:814px;height:73px;background:var(--blue);color:#fff}
.foot-links{left:88px;top:14px;font-size:9.6px;display:flex;gap:7px}
.foot-links span{opacity:.8}
.copy{left:88px;top:43px;font-size:8px}
.connect{left:653px;top:13px;font-size:11px;font-weight:500}
.social{left:653px;top:31px;display:flex;gap:4px}
.social a{width:22px;height:22px;border-radius:50%;background:#fff;display:block}
</style>
</head>
<body>

<header>
  <div class="abs brand">
    <div class="brand-name">Larkhollow</div>
    <div class="brand-sub">Consultants</div>
  </div>
  <div class="abs doctor"><span>Dr</span> XYZ</div>
  <div class="abs email">
    <svg width="15" height="11" viewBox="0 0 15 11"><rect x=".5" y=".5" width="14" height="10" fill="none" stroke="#555"/><path d="M.5 .5l7 5.5 7-5.5M.5 10.5l5-4.5M14.5 10.5l-5-4.5" fill="none" stroke="#555"/></svg>
    Email : <a href="mailto:info@larkhollow.com">info@larkhollow.com</a>
  </div>
</header>

<nav class="abs nav">
  <a href="#" style="width:86px">HOME</a>
  <a href="#" style="width:132px">CONSULTATION</a>
  <a href="#" style="width:106px">RESEARCH</a>
  <a href="#" style="width:209px">PROFESSIONAL DEVELOPMENT</a>
  <a href="#" style="width:104px">CONTACT</a>
</nav>

<div class="abs hero" role="img" aria-label="Photo of a teacher and children reading a book together in a classroom"></div>
<div class="abs hero-shadow"></div>
<div class="abs caption">We are doing consultancy practice in the area of speech, language, and reading disabilities.</div>
<div class="abs dots"><i></i><i></i><i></i><i></i></div>

<section>
  <h2 class="abs h2 welcome-title">Welcome to Our Website</h2>
  <p class="abs welcome-text">Lorem ipsum dolor sit amet, consect- etuer adipiscing elit, sed diam nonummy nibh euismod tincidunt ut laoreet dolore magna aliquam erat volutpat. Ut wisi enim ad minim veniam, quis nostrud exerci tation ullam. Consectetuer adipiscing elit, sed diam nonummy nibh euismod tincidunt ut laoreet dolore magna aliquam erat volut- pat. Ut wisi enim ad minim veniam, quis nostrud exerci tation ullam.</p>
  <a class="abs more welcome-more" href="#">READ MORE ››</a>
</section>

<section>
  <div class="abs band"></div>
  <h2 class="abs h2 what-title">What We Do</h2>

  <article class="abs card" style="left:88px">
    <div class="card-img" role="img" aria-label="Photo of a child using a tablet with an adult" style="background:linear-gradient(120deg,#6b6a2a,#9a9450 50%,#d8cfc4)"></div>
    <h3>ASSISTIVE TECHNOLOGY</h3>
    <p>Lorem ipsum dolor sit amet, consect- etuer adipiscing elit, sed diam nonummy nibh euismod tincidunt ut laoreet dolore magna...</p>
    <a class="learn" href="#">Learn More ››</a>
  </article>
  <div class="abs card-shadow" style="left:98px"></div>

  <article class="abs card" style="left:305px">
    <div class="card-img" role="img" aria-label="Photo of a young boy talking with a woman" style="background:linear-gradient(120deg,#f4ece6,#e4c8b4 45%,#4a3a34)"></div>
    <h3>EARLY LANGUAGE LEARNING</h3>
    <p>Lorem ipsum dolor sit amet, consect- etuer adipiscing elit, sed diam nonummy nibh euismod tincidunt ut laoreet dolore magna...</p>
    <a class="learn" href="#">Learn More ››</a>
  </article>
  <div class="abs card-shadow" style="left:315px"></div>

  <article class="abs card" style="left:522px">
    <div class="card-img" role="img" aria-label="Photo of a father and son reading a book on a sofa" style="background:linear-gradient(120deg,#dfe3ea,#5a6478 45%,#e8e6e2)"></div>
    <h3>READING DIFFICULTIES</h3>
    <p>Lorem ipsum dolor sit amet, consect- etuer adipiscing elit, sed diam nonummy nibh euismod tincidunt ut laoreet dolore magna...</p>
    <a class="learn" href="#">Learn More ››</a>
  </article>
  <div class="abs card-shadow" style="left:532px"></div>
</section>

<section>
  <h2 class="abs sec-title research-title">Research Updates 365</h2>
  <div class="abs research-img" role="img" aria-label="Photo of a fountain pen over a dictionary entry for research"></div>
  <ul class="abs bullets">
    <li><svg width="9" height="8" viewBox="0 0 9 8"><path d="M1 4l2.5 2.5L8 1" fill="none" stroke="#1b78d8" stroke-width="1.8"/></svg>Using assistive technology for communication for children with autism..</li>
    <li><svg width="9" height="8" viewBox="0 0 9 8"><path d="M1 4l2.5 2.5L8 1" fill="none" stroke="#1b78d8" stroke-width="1.8"/></svg>Early intervention with focus on parent participation</li>
    <li><svg width="9" height="8" viewBox="0 0 9 8"><path d="M1 4l2.5 2.5L8 1" fill="none" stroke="#1b78d8" stroke-width="1.8"/></svg>Language learning for children birth-to-five years</li>
  </ul>
  <a class="abs more research-more" href="#">READ MORE ››</a>

  <h2 class="abs sec-title pd-title">Professional development</h2>
  <div class="abs pd-item" style="top:988px">
    <div class="pd-thumb" role="img" aria-label="Photo of a presenter addressing a seminar audience" style="background:linear-gradient(135deg,#cfd6de,#3a4658)"></div>
    <div><p>Lorem ipsum dolor sit amet, consect- etuer adipiscing elit, sed di nonummy tincidunt ut laoreet dolore magna</p><b>-MARA</b></div>
  </div>
  <div class="abs pd-item" style="top:1052px">
    <div class="pd-thumb" role="img" aria-label="Photo of a group of professionals" style="background:linear-gradient(135deg,#e6e8ea,#2e3440)"></div>
    <div><p>Lorem ipsum dolor sit amet, consect- etuer adipiscing elit, sed di nonummy tincidunt ut laoreet dolore magna</p><b>-MARA</b></div>
  </div>
</section>

<footer class="abs footer">
  <div class="abs foot-links">
    <a href="#">Home</a><span>/</span><a href="#">Consultation</a><span>/</span><a href="#">Research</a><span>/</span><a href="#">Professional Development</a><span>/</span><a href="#">Contact</a>
  </div>
  <div class="abs copy">Copyright © 2014. Larkhollow Consultants. All Right Reserved</div>
  <div class="abs connect">Connect Us:</div>
  <div class="abs social">
    <a href="#" aria-label="Social link one"></a>
    <a href="#" aria-label="Social link two"></a>
    <a href="#" aria-label="Social link three"></a>
  </div>
</footer>

</body>
</html>
```